Website for Torvel Capital - investment banking firm

We have a corporate identity (thanks to Ravinka/31842) and want to extend that into a website design.  See the attached zipped files.
We have software folks in-house to do the coding.
See the attached Project Brief & Notes for more details.  Don't worry about the actual text - lorem ipsum will be fine.
The server will be Apache.
Thank you!
Desmond

Industry/Entity Type
Investment

```html
<!DOCTYPE html>
<html lang="en">
<head>
<meta charset="utf-8">
<title>Torvel Capital</title>
<link rel="stylesheet" href="https://fonts.googleapis.com/css2?family=Open+Sans:ital,wght@0,400;0,600;1,400&display=swap">
<style>
:root{
  --blue:#1f4e96;
  --blue-nav:#20509a;
  --blue-active:#3a70c0;
  --heading:#2a56a0;
  --text:#444;
  --text-dark:#222;
  --muted:#666;
  --footer:#d9e3f3;
  --testimony-bg:#f8f6f7;
  --white:#fff;
}
*{margin:0;padding:0;box-sizing:border-box}
html,body{width:1200px;height:2410px;overflow:hidden;background:var(--white)}
body{font-family:"Open Sans",Arial,sans-serif;color:var(--text);position:relative}
.abs{position:absolute}
.brand{left:144px;top:28px;display:flex;align-items:center;gap:10px;font-size:22px;font-weight:600;color:var(--blue);letter-spacing:.5px}
.brand-mark{width:30px;height:30px;background:var(--blue);border-radius:50%}
.nav{left:132px;top:95px;width:936px;height:53px;background:var(--blue-nav);display:flex}
.nav a{color:var(--white);text-decoration:none;font-size:13.5px;font-weight:600;display:flex;align-items:center;justify-content:center;border-right:1px solid #17407e}
.nav a.active{background:var(--blue-active)}
.hero{left:132px;top:148px;width:936px;height:382px;background:linear-gradient(160deg,#d8eef8 0%,#8cc6e6 35%,#5aa8d6 60%,#7fd0b0 100%)}
.hero-title{position:absolute;left:0;right:0;top:142px;text-align:center;font-size:30px;font-weight:600;color:#3a3a3a;line-height:44px}
.hero-arrow{position:absolute;top:174px}
h1,h2{font-weight:400;color:var(--heading)}
h1{font-size:26px}
h2{font-size:25px}
h3{font-size:14.5px;font-weight:400;color:var(--text-dark)}
p,li{font-size:11.5px;line-height:21px}
.intro{left:147px;top:563px;width:910px}
.intro p{margin-top:20px}
.who{left:147px;top:715px;width:910px}
.who h3{margin-top:20px}
.who p{margin-top:6px}
.photo{border-radius:8px;border:1px solid #ddd}
.process-photo{left:148px;top:927px;width:337px;height:194px;background:linear-gradient(135deg,#f4f4f4,#d9d9d9 55%,#9e8a7a)}
.process{left:496px;top:921px;width:556px}
.bullets{list-style:none;margin-top:6px}
.bullets li{padding-left:22px;position:relative;margin-bottom:3px}
.bullets li::before{content:"";position:absolute;left:8px;top:7px;width:6px;height:6px;background:#111;transform:rotate(45deg)}
.team{left:148px;top:1150px;width:530px}
.team p{font-size:12px;line-height:21px}
.team-photo{left:702px;top:1163px;width:347px;height:194px;background:linear-gradient(135deg,#3a2e28,#8a6a55 45%,#c7a98e 60%,#2f2b2a)}
.what{left:147px;top:1417px}
.card{top:1489px;width:269px}
.card-img{height:165px;border-radius:6px;position:relative;overflow:hidden}
.card-cap{position:absolute;left:0;right:0;bottom:0;height:48px;background:rgba(20,20,20,.72);color:var(--white);font-size:15px;display:flex;align-items:center;justify-content:center;text-align:center;line-height:19px}
.card p{margin-top:13px;text-align:justify;font-size:11.5px;line-height:21.5px}
.card .more{margin-top:18px;font-style:italic;font-size:12.5px;color:var(--muted)}
.testimonies{left:147px;top:1925px}
.quote-box{left:145px;top:1982px;width:909px;height:151px;background:var(--testimony-bg)}
.quote{position:absolute;left:56px;top:22px;width:805px;font-style:italic;font-size:12.5px;line-height:23px;color:#555}
.quote-by{position:absolute;left:60px;top:112px;font-style:italic;font-size:11.5px;color:#555}
.q-arrow{position:absolute;top:66px}
.footer{left:0;top:2170px;width:1200px;height:197px;background:var(--footer)}
.footer-nav{position:absolute;left:144px;top:22px;display:flex;gap:34px;font-size:11.5px;color:#555}
.contact{position:absolute;left:143px;top:72px;width:520px}
.contact h4{font-weight:400;font-size:14px;color:#444}
.contact p{margin-top:10px;font-size:11.5px;line-height:22px;color:#555}
.contact b{font-weight:600;color:#333}
.offices{position:absolute;left:823px;top:20px;width:300px;font-size:11.5px;line-height:22px;color:#555}
.offices strong{font-size:14px;font-weight:600;color:#444}
.offices .dallas{margin-top:18px}
.copyright{right:145px;top:2380px;font-size:11.5px;color:#555}
</style>
</head>
<body>

<div class="abs brand"><span class="brand-mark"></span>Torvel Capital</div>

<nav class="abs nav">
  <a class="active" style="width:149px">Home</a>
  <a style="width:135px">About</a>
  <a style="width:146px">Services</a>
  <a style="width:235px">Current Engagements</a>
  <a style="width:271px;border-right:0">Completed Transactions</a>
</nav>

<section class="abs hero" role="img" aria-label="World map with glowing network lines across continents">
  <svg class="hero-arrow" style="left:10px" width="26" height="26" viewBox="0 0 26 26"><circle cx="13" cy="13" r="12" fill="#fff" fill-opacity=".75"/><path d="M16 7 L8 13 L16 19Z" fill="#555"/></svg>
  <svg class="hero-arrow" style="right:8px" width="26" height="26" viewBox="0 0 26 26"><circle cx="13" cy="13" r="12" fill="#fff" fill-opacity=".75"/><path d="M10 7 L18 13 L10 19Z" fill="#555"/></svg>
  <div class="hero-title">Global, Professional, Trusted…<br>or Disciplined / Effective</div>
</section>

<section class="abs intro">
  <h1>Global, Professional, Trusted… or Disciplined / Effective?</h1>
  <p>Torvel Capital is an independent investment bank working for buyers in a number of industries. We utilize exceptional technology in finding companies to meet our client's search criteria. We will not waste a buyer's time, a seller's time, or our own time.</p>
</section>

<section class="abs who">
  <h2>Who We Are ?</h2>
  <h3>Our Name</h3>
  <p>Use the word "Torvel" – "exuberant energy" to leverage Asian–Pacific market concept.</p>
  <h3 style="margin-top:22px">Our Clients</h3>
  <p>Torvel Capital has a diverse array of clients ranging from multi-billion dollar strategic acquirers to large private equity funds. We will not engage a client as a buyer if we believe there is any chance of them wasting our time or a prospective seller's time.</p>
</section>

<div class="abs photo process-photo" role="img" aria-label="Businessman sketching a flowchart on a glass board"></div>

<section class="abs process">
  <h3>Our Process</h3>
  <ul class="bullets">
    <li>Technology</li>
    <li>Once we have your acquisition parameters, we feed these into our software to create an initial target list. The criteria used to create this list can include geography, revenue targets, earning targets, margins, shareholder structure, etc. When our software has identified a qualified list, Torvel will reach out to prospective sellers. With Torvel Capital's technology, we are likely to know at any point in time who is interested in selling as a result.</li>
    <li>Process</li>
    <li>Professional discipline</li>
  </ul>
</section>

<section class="abs team">
  <h3>Team</h3>
  <ul class="bullets">
    <li>Experienced professionals supported by expert research team and sophisticated technology</li>
    <li>Torvel Capital's team of bankers and advisors comprised of experienced professionals.</li>
  </ul>
  <p>Our research team is critical in finding deals where there sufficient strategic overlap that will result in a deal valuation and structure that will work for both buyer and seller. Simply said, we find deals that nobody else can.</p>
  <ul class="bullets" style="margin-top:4px">
    <li>Our experienced professionals have international experience from range backgrounds</li>
  </ul>
  <p>such engineering, accounting, executive management and software programming several have been business owners.</p>
</section>

<div class="abs photo team-photo" role="img" aria-label="Group portrait of the firm's team"></div>

<h2 class="abs what">What We Do ?</h2>

<article class="abs card" style="left:148px">
  <div class="card-img" role="img" aria-label="City skyline with a signpost reading buy" style="background:linear-gradient(180deg,#9fb8d8 0%,#c7d4e2 45%,#8a7a62 75%,#5b4e40 100%)"><div class="card-cap">Buy-Side Acquisitions</div></div>
  <p>We assist corporate clients and private equity groups to identify opportunities for growth by acquisition We understand the lower middle market intimately, and we know the market dynamics unique to each sector.<br>We've can give buyers access to sophisticated software tools that enable your target</p>
  <div class="more">More...</div>
</article>

<article class="abs card" style="left:466px">
  <div class="card-img" role="img" aria-label="Hands reviewing financial charts with a pen" style="background:linear-gradient(135deg,#1c2e5a 0%,#e8eef6 40%,#9fb4d4 70%,#1a2a4e 100%)"><div class="card-cap">Recapitalizations<br>&amp; Growth Capital Partnerships</div></div>
  <p>We assist corporate clients and private equity groups to identify opportunities for growth by acquisition We understand the lower middle market intimately, and we know the market dynamics unique to each sector.<br>We've can give buyers access to sophisticated software tools that enable your target</p>
  <div class="more">More...</div>
</article>

<article class="abs card" style="left:780px">
  <div class="card-img" role="img" aria-label="Business handshake" style="background:linear-gradient(135deg,#5a5a5a 0%,#c9a27e 45%,#e6c4a0 60%,#6b6b6b 100%)"><div class="card-cap">Sell-Side Transactions</div></div>
  <p>We assist corporate clients and private equity groups to identify opportunities for growth by acquisition We understand the lower middle market intimately, and we know the market dynamics unique to each sector.<br>We've can give buyers access to sophisticated software tools that enable your target</p>
  <div class="more">More...</div>
</article>

<h2 class="abs testimonies">Testimonies</h2>

<section class="abs quote-box">
  <svg class="q-arrow" style="left:8px" width="16" height="16" viewBox="0 0 16 16"><path d="M14 2 L2 8 L14 14Z" fill="#555"/></svg>
  <svg class="q-arrow" style="right:8px" width="16" height="16" viewBox="0 0 16 16"><path d="M2 2 L14 8 L2 14Z" fill="#555"/></svg>
  <p class="quote">“ Sed ut perspiciatis unde omnis iste natus error sit voluptatem accusantium doloremque laudantium, totam rem aperiam, eaque ipsa quae ab illo inventore veritatis Nemo enim ipsamor sit voluptatem accusantium doloremque laudantium, totam rem ap voluptatem quia voluptas sit aspernaturor sit voluptatem accusantium doloremque laudantium, totam rem ap ”</p>
  <div class="quote-by">- - Harbour Ledger</div>
</section>

<footer class="abs footer">
  <div class="footer-nav"><span>Home</span><span>About</span><span>Services</span><span>Current Engagements</span><span>Completed Transactions</span></div>
  <div class="contact">
    <h4>Contact Us :</h4>
    <p>Torvel Capital maintains offices in China, Japan, the USA and Canada. We will respond to your enquiries rapidly. Please contact us at the email address below<br>E-mail: <b>info@torvelcapital.com</b></p>
  </div>
  <div class="offices">
    <div><strong>Hong Kong :</strong> Room 1408 Harbourline Tower<br>88 Lockhart Road East<br>Wanchai, Hong Kong</div>
    <div class="dallas"><strong>Dallas :</strong> 1740 Meridian Parkway, Suite 310<br>Plano, Texas 75024<br>Telephone: 469-555-0147</div>
  </div>
</footer>

<div class="abs copyright">Torvel Capital© 2014. All Rights Reserved.</div>

</body>
</html>
```